Therapy and counselling practice needs a compelling double-sided promotional flyer

We need someone to design a highly engaging, easy to read, revenue generating promotional flyer that we can give to potential new clients. I have attached the content I need you to include, as well as the professional photo of myself and the company logo. Please use a colour scheme which matches the colours used in my logo. Our website is www.velmaro.com.au for reference to our practice. Need something that looks really modern and eye catching and positions the content in a way which isn't just like a jazzed up Word document.

Please also feel free to use additional images as you deem appropriate, relating to therapy / counselling with clients. See my website for examples - velmaro.com.au

```html
<!DOCTYPE html>
<html lang="en">
<head>
<meta charset="utf-8">
<title>Velmaro Health Services – Counselling Flyer</title>
<link href="https://fonts.googleapis.com/css2?family=Outfit:wght@300;400;500;600;700&display=swap" rel="stylesheet">
<style>
:root{
  --red:#e0232b;
  --yellow:#ffd400;
  --ink:#111111;
  --body:#3a3a3a;
  --dark:#252525;
  --stage:#adadad;
  --white:#ffffff;
  --navy:#2c3a52;
}
*{box-sizing:border-box;margin:0;padding:0}
html,body{width:1200px;height:800px;overflow:hidden}
body{background:var(--stage);font-family:'Outfit',sans-serif;color:var(--body);position:relative}
.page{position:absolute;background:var(--white);overflow:hidden}
.page--front{left:67px;top:67px;width:523px;height:676px}
.page--back{left:626px;top:69px;width:520px;height:673px}
.abs{position:absolute}

/* brand */
.brand{left:24px;top:44px;display:flex;align-items:center;gap:7px}
.brand__dot{width:14px;height:14px;border-radius:50%;background:var(--red)}
.brand__name{font-weight:700;font-size:30px;line-height:1;color:var(--ink)}

.hero-title{left:24px;top:104px;font-weight:700;font-size:23.5px;line-height:29px;color:var(--ink)}
.hero-intro{left:24px;top:197px;width:232px;font-size:7.2px;line-height:9.3px;font-weight:300;color:var(--body)}

.hero-art{left:0;top:0;width:523px;height:330px}
.portrait{left:0;top:265px;width:250px;height:352px}
.person-name{left:0;top:570px;width:210px;text-align:center;color:var(--white)}
.person-name__n{font-size:16.5px;font-weight:500}
.person-name__r{font-size:8.4px;font-weight:300}

.cta-band{background:var(--yellow);color:var(--ink);font-weight:600;font-size:16px;display:flex;align-items:center}
.page--front .cta-band{left:0;top:615px;width:262px;height:26px;padding-left:20px;border-top-right-radius:22px}
.page--back .cta-band{left:239px;top:604px;width:281px;height:33px;justify-content:center;border-top-left-radius:26px}

.footer{left:0;width:100%;background:var(--dark);color:var(--white);display:flex;align-items:center;gap:20px;font-size:14px;font-weight:500}
.page--front .footer{top:641px;height:35px;padding-left:24px}
.page--back .footer{top:637px;height:36px;padding-left:24px}
.footer__item{display:flex;align-items:center;gap:4px;white-space:nowrap}
.footer__item svg{width:12px;height:12px}

.why-pill{left:211px;top:282px;width:294px;height:29px;border-radius:14px 14px 0 0;background:linear-gradient(90deg,#111,#333 60%,#111);color:var(--white);font-size:15px;font-weight:500;display:flex;align-items:center;justify-content:center}

.icon-badge{width:46px;height:46px;border-radius:50%;background:var(--red);display:flex;align-items:center;justify-content:center;box-shadow:0 0 0 2px #fff}
.icon-badge svg{width:24px;height:24px}
.rail{width:0;border-left:1px dashed #9a9a9a}

.block h3{font-weight:600;font-size:13.5px;line-height:16px;color:var(--ink)}
.block p{font-size:8.2px;line-height:10.9px;font-weight:300;margin-top:6px}
.block .indent{padding-left:17px;margin-top:5px}
.block .strong{font-weight:600;color:var(--ink)}
.ticks{list-style:none;margin-top:5px}
.ticks li{position:relative;padding-left:12px;font-size:8.2px;line-height:10.9px;font-weight:300;margin-bottom:3px}
.ticks li::before{content:"";position:absolute;left:0;top:3px;width:6px;height:6px;border-radius:50%;background:var(--yellow)}
.ticks b{font-weight:600;color:var(--ink)}

.contact{left:33px;top:602px;color:var(--ink)}
.contact__n{font-size:17px;font-weight:600;line-height:18px}
.contact__r{font-size:8.2px;font-weight:300}
</style>
</head>
<body>

<section class="page page--front">
  <svg class="abs hero-art" viewBox="0 0 523 330">
    <circle cx="395" cy="55" r="192" fill="var(--red)"/>
    <circle cx="395" cy="55" r="178" fill="var(--yellow)"/>
    <circle cx="395" cy="55" r="168" fill="#fff"/>
    <circle cx="395" cy="55" r="164" fill="#c9ced3" role="img" aria-label="Photo of a young man talking with a counsellor during a session"/>
    <circle cx="321" cy="191" r="64" fill="#fff"/>
    <circle cx="321" cy="191" r="60" fill="#b7aea3" role="img" aria-label="Photo of a carer comforting an older man"/>
  </svg>

  <div class="abs brand">
    <span class="brand__dot"></span>
    <span class="brand__name">Velmaro</span>
  </div>

  <h1 class="abs hero-title">Reclaim Your<br>Well-Being with<br>Expert Counselling</h1>
  <p class="abs hero-intro">Life's challenges and traumas can sometimes feel overwhelming. At Velmaro Health Services, we believe in your potential to overcome obstacles and lead a meaningful, fulfilling life. As a highly qualified therapist and counsellor, my name is Marcus Heller, and I'm here to support you on your journey every step of the way.</p>

  <div class="abs portrait" role="img" aria-label="Portrait of the lead therapist in a dark suit" style="background:linear-gradient(180deg,#fff 0%,#fff 12%,#5a6a80 45%,var(--navy) 100%);border-radius:120px 120px 0 0"></div>
  <div class="abs person-name">
    <div class="person-name__n">Marcus Heller</div>
    <div class="person-name__r">Practice Owner and Lead Therapist</div>
  </div>

  <div class="abs why-pill">Why Choose Me as Your Therapist?</div>

  <div class="abs rail" style="left:232px;top:370px;height:250px"></div>
  <div class="abs icon-badge" style="left:209px;top:323px">
    <svg viewBox="0 0 24 24" fill="none" stroke="#fff" stroke-width="1.6"><circle cx="12" cy="12" r="9"/><circle cx="12" cy="12" r="4"/></svg>
  </div>
  <div class="abs icon-badge" style="left:209px;top:518px">
    <svg viewBox="0 0 24 24" fill="none" stroke="#fff" stroke-width="1.6"><rect x="5" y="3" width="14" height="18" rx="1"/><path d="M8 8h8M8 12h8M8 16h5"/></svg>
  </div>

  <div class="abs block" style="left:263px;top:334px;width:245px">
    <h3>Comprehensive Expertise</h3>
    <p>I bring a unique combination of skills and experience to my counselling practice, blending years of corporate leadership with a deep understanding of mental health. My background includes:</p>
    <p class="indent">Over a decade in corporate roles, specialising in leadership development, workplace culture, and HR strategy.<br>Consulting experience with small to medium-sized enterprises, focusing on leadership coaching and employee engagement.</p>
    <p>This foundation allows me to offer unique insights into the challenges faced by professionals and leaders, including work-related stress, burnout, and interpersonal dynamics.</p>
  </div>

  <div class="abs block" style="left:263px;top:527px;width:245px">
    <h3>Extensive Qualifications</h3>
    <p>I bring a solid foundation of academic and professional experience, including:</p>
    <p class="indent">Diploma of Counselling (Southern Institute of Counselling Studies).<br>Certified Adolescent Counsellor (Coastline University).<br>Postgraduate qualifications in Human Resource Management.</p>
  </div>

  <div class="abs cta-band">to schedule your consultation</div>
  <div class="abs footer">
    <span class="footer__item"><svg viewBox="0 0 24 24" fill="var(--yellow)"><path d="M6 2l4 4-2 3c1 3 4 6 7 7l3-2 4 4-3 4C10 21 3 14 2 5z"/></svg>(03) 9000 4128</span>
    <span class="footer__item"><svg viewBox="0 0 24 24" fill="none" stroke="var(--yellow)" stroke-width="2"><rect x="2" y="5" width="20" height="14"/><path d="M2 5l10 8 10-8"/></svg>marcus@velmaro.com.au</span>
    <span class="footer__item"><svg viewBox="0 0 24 24" fill="none" stroke="var(--yellow)" stroke-width="2"><circle cx="12" cy="12" r="10"/><path d="M2 12h20M12 2c4 4 4 16 0 20M12 2c-4 4-4 16 0 20"/></svg>www.velmaro.com.au</span>
  </div>
</section>

<section class="page page--back">
  <div class="abs rail" style="left:47px;top:80px;height:480px"></div>
  <div class="abs rail" style="left:277px;top:80px;height:400px"></div>

  <div class="abs icon-badge" style="left:24px;top:28px"><svg viewBox="0 0 24 24" fill="none" stroke="#fff" stroke-width="1.6"><rect x="4" y="4" width="16" height="16" rx="3"/><path d="M8 10h8M8 14h5"/></svg></div>
  <div class="abs icon-badge" style="left:24px;top:243px"><svg viewBox="0 0 24 24" fill="none" stroke="#fff" stroke-width="1.6"><circle cx="12" cy="8" r="3"/><path d="M5 20c1-5 13-5 14 0"/></svg></div>
  <div class="abs icon-badge" style="left:24px;top:534px"><svg viewBox="0 0 24 24" fill="none" stroke="#fff" stroke-width="1.6"><path d="M4 20h16M6 16h12M8 12h8M12 4v5"/></svg></div>
  <div class="abs icon-badge" style="left:254px;top:28px"><svg viewBox="0 0 24 24" fill="none" stroke="#fff" stroke-width="1.6"><circle cx="12" cy="9" r="4"/><path d="M5 20c1-5 13-5 14 0"/></svg></div>
  <div class="abs icon-badge" style="left:254px;top:302px"><svg viewBox="0 0 24 24" fill="none" stroke="#fff" stroke-width="1.6"><path d="M12 3l7 3v6c0 5-4 8-7 9-3-1-7-4-7-9V6z"/><path d="M9 12l2 2 4-4"/></svg></div>
  <div class="abs icon-badge" style="left:254px;top:428px"><svg viewBox="0 0 24 24" fill="none" stroke="#fff" stroke-width="1.6"><rect x="3" y="4" width="18" height="12" rx="1"/><path d="M8 20h8M12 16v4"/></svg></div>

  <div class="abs block" style="left:78px;top:30px;width:172px">
    <h3>Specialised Therapeutic Techniques</h3>
    <p>At Velmaro Health Services, I use evidence-based approaches tailored to your individual needs</p>
    <ul class="ticks">
      <li><b>Cognitive Behavioural Therapy (CBT):</b> Helping you identify and reframe unhelpful thought patterns.</li>
      <li><b>Acceptance and Commitment Therapy (ACT):</b> Supporting you to embrace challenges while staying committed to your values.</li>
      <li><b>Motivational Questioning:</b> Encouraging meaningful change by exploring your strengths and aspirations.</li>
    </ul>
  </div>

  <div class="abs block" style="left:78px;top:245px;width:172px">
    <h3>A Unique Counselling Approach</h3>
    <p>I take a person-centred approach to therapy, creating a safe, confidential, and supportive environment where you can openly explore your concerns. My goal is to empower you to:</p>
    <ul class="ticks" style="margin-top:8px">
      <li><b>Navigate and heal from trauma. Develop resilience and coping strategies.</b></li>
      <li><b>Improve relationships and communication.</b></li>
      <li><b>Achieve personal growth and fulfilment.</b></li>
    </ul>
    <p>Whether you are seeking support as an individual or as a couple, I am experienced in addressing a variety of challenges, including relationship dynamics, communication breakdowns, and emotional well-being. Together, we will work towards fostering stronger connections and healthier relationships.</p>
  </div>

  <div class="abs block" style="left:308px;top:30px;width:192px">
    <h3>Trauma-Informed<br>Care</h3>
    <p>As a trauma-informed counsellor, I understand the profound impact that trauma can have on mental, emotional, and physical well-being. Trauma-informed care means recognising the prevalence of trauma, understanding its effects, and creating a safe, supportive environment for healing.</p>
    <p class="strong">This approach benefits clients by:</p>
    <ul class="ticks" style="margin-top:7px">
      <li>Ensuring that therapy is sensitive to past experiences and avoids re-traumatisation.</li>
      <li>Helping clients build trust and safety in the therapeutic relationship.</li>
      <li>Empowering individuals to regain control, develop resilience, and move forward with confidence.</li>
    </ul>
    <p>Whether you're dealing with childhood trauma, grief, or life-altering events, I'm here to help you navigate your journey towards healing and recovery.</p>
  </div>

  <div class="abs block" style="left:308px;top:305px;width:192px">
    <h3>Modern and Trusted Counselling Practice</h3>
    <p>Based in Seabrook Victoria, Velmaro Health Services is a full-service counselling practice dedicated to supporting individuals across various life stages. Our focus is on delivering impactful results through tailored, individualised therapy that addresses your unique challenges.</p>
  </div>

  <div class="abs block" style="left:308px;top:431px;width:192px">
    <h3>Online Counselling for Your Convenience</h3>
    <p>All sessions are conducted online via Meetly, enabling me to reach a broader audience nationally while keeping sessions cost-effective. This flexible approach allows you to access high-quality counselling from the comfort of your own home, wherever you are located.</p>
  </div>

  <div class="abs block" style="left:78px;top:537px;width:410px">
    <h3>Take the First Step Today</h3>
    <p>Your journey to well-being starts with a conversation. Whether you're seeking to overcome trauma, manage mental health challenges, or navigate life's transitions, I'm here to support you.</p>
  </div>

  <div class="abs contact">
    <div class="contact__n">Contact Marcus Heller</div>
    <div class="contact__r">Practice Owner and Lead Therapist</div>
  </div>

  <div class="abs cta-band">to schedule your consultation</div>
  <div class="abs footer">
    <span class="footer__item"><svg viewBox="0 0 24 24" fill="var(--yellow)"><path d="M6 2l4 4-2 3c1 3 4 6 7 7l3-2 4 4-3 4C10 21 3 14 2 5z"/></svg>(03) 9000 4128</span>
    <span class="footer__item"><svg viewBox="0 0 24 24" fill="none" stroke="var(--yellow)" stroke-width="2"><rect x="2" y="5" width="20" height="14"/><path d="M2 5l10 8 10-8"/></svg>marcus@velmaro.com.au</span>
    <span class="footer__item"><svg viewBox="0 0 24 24" fill="none" stroke="var(--yellow)" stroke-width="2"><circle cx="12" cy="12" r="10"/><path d="M2 12h20M12 2c4 4 4 16 0 20M12 2c-4 4-4 16 0 20"/></svg>www.velmaro.com.au</span>
  </div>
</section>

</body>
</html>
```